Mobile App UI for Telecommunications/Hosting Company

We are about to convert our existing self-service Customer Portal into a mobile phone application and need an elegant and professional UI/UX design. Our company provides telecommunication (voice/mobile/data) and hosting services to medium-sized business. The primary purpose of the application is to view trouble tickets, alerts, orders, and performance charts. This application is available to customers only - not the general public.

Please provide a UI design suitable for display on iPhone/Android devices. The attached document includes a proposed screen flow. You are free to design your own screens to display the same information elegantly.
Updates

Please note that the design should be based on the wireframes in the Word document, not the screenshots.  The screenshots are just to show our existing web portal look & feel.

Also, just a few screens are required for initial submission (3 would be great).

Thanks,
Dermot.

Target Market(s)

IT Managers away from their desk and using a mobile phone application.
Adult males from technical background aged 30-50.
Customers of Brindlewood Telecom have access to this application (not the general public). This is a self-service portal for customers only.

Industry/Entity Type

Business

Colors
0592cd
33a6d7
85cae6
cadf82
fde08a

Requirements
Must have
• Please look at the screenshots from our current Customer Portal site (part of the project brief). The mobile app does not have to look the same, but should follow a similar style.

Please check out our company web site at www.brindlewoodtelecom.example (this site is not the customer portal and has a different look at feel) to understand what Brindlewood Telecom does.
Nice to have
• Sharing capabilities via email/SMS.
A nice background image to make it stand out
The colours selected below are a guide only as they are similar to the corporate colours
- The priority is something that works on a phone - a design extendable to tablets is a nice to have as our existing web site looks OK on a tablet..

```html
<!DOCTYPE html>
<html lang="en">
<head>
<meta charset="utf-8">
<title>Brindlewood View – Alerts</title>
<link rel="stylesheet" href="https://fonts.googleapis.com/css2?family=Open+Sans:wght@300;400;600&display=swap">
<style>
  :root {
    --sidebar-top: #fbdf8c;
    --sidebar-bottom: #e6df86;
    --sidebar-line: #f1d57e;
    --icon: #ffffff;
    --menu-cell: #ffffff;
    --menu-icon: #555555;
    --header-bg: #8ec6d8;
    --hero-top: #4f9fbe;
    --hero-bottom: #9fd3e3;
    --list-top: #f7f8f5;
    --list-bottom: #d9dfe8;
    --row-line: #d9d7d0;
    --row-alt: rgba(120, 120, 110, 0.10);
    --date-text: #3a3a3a;
    --status-text: #9a9a9a;
    --status-alert: #e2506e;
    --white: #ffffff;
  }
  * { margin: 0; padding: 0; box-sizing: border-box; }
  html, body { width: 676px; height: 1200px; overflow: hidden; background: #ffffff; }
  body { font-family: "Open Sans", Arial, sans-serif; }

  .app { position: relative; width: 676px; height: 1200px; overflow: hidden; }

  .sidebar {
    position: absolute; left: 0; top: 0; width: 120px; height: 1200px;
    background: linear-gradient(180deg, var(--sidebar-top), var(--sidebar-bottom));
  }
  .menu-toggle {
    height: 101px; background: var(--menu-cell);
    display: flex; align-items: center; justify-content: center;
  }
  .nav-item {
    height: 127px; display: flex; align-items: center; justify-content: center;
    border-bottom: 2px solid var(--sidebar-line);
  }
  .nav-item svg { width: 52px; height: 52px; fill: none; stroke: var(--icon); stroke-width: 2.6; stroke-linecap: round; stroke-linejoin: round; }
  .nav-item:nth-child(n+6) { border-bottom: none; }

  .topbar {
    position: absolute; left: 120px; top: 0; width: 556px; height: 101px;
    background: var(--header-bg);
    display: flex; align-items: center; justify-content: space-between;
    padding: 0 24px 0 24px;
  }
  .app-name { color: var(--white); font-size: 45px; font-weight: 400; letter-spacing: -0.5px; }
  .profile svg { width: 56px; height: 56px; fill: none; stroke: var(--white); stroke-width: 2.6; }

  .hero {
    position: absolute; left: 120px; top: 101px; width: 556px; height: 262px;
    background: linear-gradient(180deg, var(--hero-top), var(--hero-bottom));
    color: var(--white);
  }
  .hero-title { position: absolute; left: 28px; top: 82px; font-size: 56px; font-weight: 400; letter-spacing: 2px; line-height: 1; }
  .hero-date { position: absolute; left: 30px; top: 150px; font-size: 27px; font-weight: 600; letter-spacing: 1px; color: rgba(255,255,255,0.85); }
  .hero-count { position: absolute; left: 296px; top: 44px; font-size: 146px; font-weight: 400; line-height: 1; }

  .alert-list {
    position: absolute; left: 120px; top: 363px; width: 556px; height: 837px;
    background: linear-gradient(180deg, var(--list-top), var(--list-bottom));
    list-style: none;
  }
  .alert-list::after {
    content: ""; position: absolute; left: 357px; top: 0; width: 2px; height: 100%;
    background: var(--row-line);
  }
  .alert-row {
    height: 126px; display: flex; align-items: center;
    border-bottom: 2px solid var(--row-line);
  }
  .alert-row:last-child { border-bottom: none; height: 207px; align-items: flex-start; padding-top: 44px; }
  .alert-row.is-selected { background: var(--row-alt); }
  .alert-date { width: 358px; padding-left: 32px; font-size: 32px; color: var(--date-text); }
  .alert-status { flex: 1; text-align: center; font-size: 34px; color: var(--status-text); }
  .alert-status.is-alert { color: var(--status-alert); }
</style>
</head>
<body>
<div class="app">
  <nav class="sidebar">
    <div class="menu-toggle">
      <svg width="48" height="36" viewBox="0 0 48 36"><rect x="0" y="2" width="48" height="6" fill="#555"/><rect x="0" y="15" width="48" height="6" fill="#555"/><rect x="0" y="28" width="48" height="6" fill="#555"/></svg>
    </div>
    <div class="nav-item" aria-label="Messages">
      <svg viewBox="0 0 52 52"><rect x="5" y="12" width="42" height="28" rx="5"/><path d="M6 14 L26 29 L46 14"/></svg>
    </div>
    <div class="nav-item" aria-label="Orders">
      <svg viewBox="0 0 52 52"><path d="M6 24 L46 6 L34 46 L24 30 Z"/><path d="M24 30 L46 6"/><path d="M24 30 L22 44 L30 36"/></svg>
    </div>
    <div class="nav-item" aria-label="Calendar">
      <svg viewBox="0 0 52 52"><rect x="7" y="10" width="38" height="36" rx="4"/><path d="M7 20 H45 M16 5 V14 M36 5 V14 M18 28 V38 M26 28 V38 M34 28 V38"/></svg>
    </div>
    <div class="nav-item" aria-label="Performance">
      <svg viewBox="0 0 52 52"><path d="M4 36 L16 22 L26 30 L36 18 L48 28"/></svg>
    </div>
    <div class="nav-item" aria-label="New ticket">
      <svg viewBox="0 0 52 52"><circle cx="26" cy="26" r="20"/><path d="M26 16 V36 M16 26 H36"/></svg>
    </div>
    <div class="nav-item" aria-label="Watch list">
      <svg viewBox="0 0 52 52"><path d="M3 26 C13 12 39 12 49 26 C39 40 13 40 3 26 Z"/><circle cx="26" cy="26" r="6" fill="#fff"/></svg>
    </div>
    <div class="nav-item" aria-label="Settings">
      <svg viewBox="0 0 52 52"><circle cx="26" cy="26" r="7"/><path d="M26 4 L30 10 L37 7 L38 14 L45 15 L42 22 L48 26 L42 30 L45 37 L38 38 L37 45 L30 42 L26 48 L22 42 L15 45 L14 38 L7 37 L10 30 L4 26 L10 22 L7 15 L14 14 L15 7 L22 10 Z"/></svg>
    </div>
  </nav>

  <header class="topbar">
    <span class="app-name">brindlewoodview</span>
    <span class="profile" aria-label="Account">
      <svg viewBox="0 0 56 56"><circle cx="28" cy="19" r="11"/><path d="M6 52 C8 38 17 32 28 32 C39 32 48 38 50 52 Z"/></svg>
    </span>
  </header>

  <section class="hero">
    <h1 class="hero-title">ALERTS</h1>
    <p class="hero-date">FRI&nbsp; 29/06</p>
    <p class="hero-count">24</p>
  </section>

  <ul class="alert-list">
    <li class="alert-row"><span class="alert-date">SAT 29/06</span><span class="alert-status">warning</span></li>
    <li class="alert-row is-selected"><span class="alert-date">SUN 30/06</span><span class="alert-status is-alert">warning</span></li>
    <li class="alert-row"><span class="alert-date">MON 01/07</span><span class="alert-status">warning</span></li>
    <li class="alert-row"><span class="alert-date">TUE 02/07</span><span class="alert-status">warning</span></li>
    <li class="alert-row"><span class="alert-date">WED 03/07</span><span class="alert-status">warning</span></li>
    <li class="alert-row"><span class="alert-date">THU 04/07</span><span class="alert-status">warning</span></li>
  </ul>
</div>
</body>
</html>
```